Modern Dry eye Poster for eye center, Optometrist office

We need a banner to connect to patient about dry eye and treatment. Ask if patient has dry eyes and we offer treatment .
What is dry eye?
Are you suffering for dry, gritty, painful eyes, blurred vision, redness..

Now there is a quick, comfortable and affordable procedure offering relief tofdry eye.

Schedule your dry eye treatment today.

Target Market(s)

Dry eye patient

Font styles to use
Sans Serif

Colors
00a990
ffffff
0492cd
fbf289
85cae6

Requirements
Must have
• Modern design, dry eye patient
Nice to have
• real life model of nice eyes
Should not have
• No cartoon,

```html
<!DOCTYPE html>
<html lang="en">
<head>
<meta charset="utf-8">
<title>What is dry eye? — Lumen Optometry</title>
<link href="https://fonts.googleapis.com/css2?family=Source+Sans+3:wght@400;600;700;800&family=Open+Sans:wght@700&display=swap" rel="stylesheet">
<style>
  :root {
    --sun: #f7d43f;
    --slate: #6a7676;
    --slate-dark: #5b6868;
    --paper: #ffffff;
    --skin-pale: #f3e4de;
    --skin-light: #e8cfc6;
    --skin-mid: #d6ada0;
    --skin-deep: #c0958a;
  }
  * { margin: 0; padding: 0; box-sizing: border-box; }
  html, body { width: 1200px; height: 2517px; overflow: hidden; background: var(--paper); }
  .poster {
    position: relative;
    width: 1200px;
    height: 2517px;
    background: var(--paper);
    font-family: "Source Sans 3", "Myriad Pro", sans-serif;
    color: var(--slate);
    overflow: hidden;
  }
  .hero-photo {
    position: absolute;
    left: 0; top: 500px;
    width: 1200px; height: 1250px;
    background:
      linear-gradient(to right, rgba(255,255,255,0.55) 0%, rgba(255,255,255,0) 22%, rgba(255,255,255,0) 80%, rgba(192,149,138,0.25) 100%),
      linear-gradient(to bottom,
        var(--skin-light) 0%,
        var(--skin-mid) 22%,
        var(--skin-deep) 42%,
        var(--skin-mid) 58%,
        var(--skin-pale) 78%,
        rgba(255,255,255,0) 100%);
  }
  .title-band {
    position: absolute;
    left: 0; top: 47px;
    width: 775px; height: 201px;
    background: var(--sun);
  }
  .title-band__text {
    position: absolute;
    left: 106px; top: 4px;
    font-weight: 800;
    font-size: 202px;
    line-height: 1;
    letter-spacing: -3px;
    color: var(--paper);
    white-space: nowrap;
  }
  .title-sub {
    position: absolute;
    left: 500px; top: 248px;
    font-weight: 400;
    font-size: 133px;
    line-height: 1;
    letter-spacing: -4px;
    color: var(--slate);
    white-space: nowrap;
  }
  .question {
    position: absolute;
    left: 299px; top: 412px;
    font-weight: 600;
    font-size: 60px;
    line-height: 1;
    color: var(--slate);
    white-space: nowrap;
  }
  .symptoms {
    position: absolute;
    left: 190px; top: 1370px;
    width: 900px;
    text-align: center;
    font-weight: 400;
    font-size: 54px;
    line-height: 79px;
    color: var(--slate);
    list-style: none;
  }
  .relief {
    position: absolute;
    left: 104px; top: 2040px;
    font-family: "Open Sans", "Verdana", sans-serif;
    font-weight: 700;
    font-size: 55px;
    line-height: 72px;
    color: var(--slate-dark);
    white-space: nowrap;
  }
  .cta {
    position: absolute;
    left: 104px; top: 2272px;
    font-weight: 400;
    font-size: 58px;
    line-height: 67px;
    color: var(--slate-dark);
    white-space: nowrap;
  }
  .brand {
    position: absolute;
    left: 825px; top: 2075px;
    width: 300px;
    text-align: center;
  }
  .brand__mark {
    display: block;
    width: 205px; height: 205px;
    margin: 0 auto 50px;
    background: var(--sun);
  }
  .brand__name {
    font-weight: 400;
    font-size: 31px;
    line-height: 36px;
    letter-spacing: 4px;
    color: var(--slate);
  }
</style>
</head>
<body>
<main class="poster">
  <div class="hero-photo" role="img" aria-label="Close-up photograph of a woman's green eye with long lashes, fading to white below"></div>

  <header>
    <div class="title-band"><h1 class="title-band__text">What is</h1></div>
    <p class="title-sub">dry eye?</p>
    <p class="question">Are you suffering for:</p>
  </header>

  <ul class="symptoms">
    <li>dry sensation, scratch,</li>
    <li>gritty feeling,</li>
    <li>burning, stinging, itching,</li>
    <li>excess tearing,</li>
    <li>mucous discharge, redness,</li>
    <li>light sensitivity,</li>
    <li>contact lens discomfort,</li>
    <li>soreness?</li>
  </ul>

  <p class="relief">now there is a quick,<br>comfortable, affordable<br>procedure offering relief.</p>
  <p class="cta">Schedule your dry eye<br>treatment today.</p>

  <div class="brand">
    <span class="brand__mark"></span>
    <p class="brand__name">LUMEN<br>OPTOMETRY</p>
  </div>
</main>
</body>
</html>
```